Road Construction Company needs business cards

We would like a new business card designed for our business.

We're a road construction company based in Qld, Australia.

Can the business card please have the following information on it.

Name: Warren Halbeck
Position: General Manager
Phone: 0472 915 348
Email: Warren.halbeck@tovrin.com.au
Address: 87 Marrow Ave, Pendlebay, QLD, 4023
Website: www.tovrin.com.au

Visually we'd like the card to be professional and simple.

Attached is our logo.

Our website is www.tovrin.com.au

Target Market(s)

Men aged 25-60

Contact Information for Business Card

As listed in project description

Font styles to use
Serif

Requirements
Must have
• Large logo on back of card

```html
<!DOCTYPE html>
<html lang="en">
<head>
<meta charset="utf-8">
<title>Tovrin Business Card</title>
<link href="https://fonts.googleapis.com/css2?family=Rubik:wght@400;700;800&display=swap" rel="stylesheet">
<style>
  :root {
    --stage: #8f8f8f;
    --brand-blue: #0c4da2;
    --brand-deep: #0a3f8c;
    --accent: #2f9ad8;
    --ink: #4a4a4a;
    --paper: #ffffff;
  }
  * { margin: 0; padding: 0; box-sizing: border-box; }
  html, body { width: 1200px; height: 588px; overflow: hidden; }
  body {
    background: var(--stage);
    font-family: "Rubik", sans-serif;
    position: relative;
  }
  .card {
    position: absolute;
    top: 150px;
    width: 488px;
    height: 287px;
    overflow: hidden;
  }
  .card-back { left: 90px; }
  .card-front { left: 622px; background: var(--paper); }

  .back-pattern {
    position: absolute; inset: 0;
    background: linear-gradient(120deg, #17428e 0%, #0b55a8 45%, #2f6fbf 100%);
  }
  .back-brand {
    position: absolute;
    left: 0; right: 0; top: 104px;
    text-align: center;
    font-weight: 800;
    font-size: 58px;
    letter-spacing: 2px;
    color: var(--paper);
  }

  .front-brand {
    position: absolute;
    left: 0; right: 0; top: 36px;
    text-align: center;
    font-weight: 800;
    font-size: 46px;
    letter-spacing: 2px;
    color: var(--brand-blue);
  }
  .holder {
    position: absolute;
    right: 282px; top: 177px;
    text-align: right;
  }
  .holder-name {
    font-weight: 700;
    font-size: 19px;
    color: var(--brand-blue);
    letter-spacing: 0.2px;
  }
  .holder-role {
    font-size: 13.5px;
    color: var(--ink);
    margin-top: 2px;
  }
  .divider {
    position: absolute;
    left: 228px; top: 151px;
    width: 1.5px; height: 94px;
    background: var(--brand-blue);
  }
  .contacts {
    position: absolute;
    left: 246px; top: 149px;
    list-style: none;
    font-size: 13.5px;
    color: var(--ink);
  }
  .contacts li {
    display: flex;
    align-items: flex-start;
    line-height: 18.5px;
  }
  .contacts li + li { margin-top: 0; }
  .contacts .gap { margin-top: 5px; }
  .contacts svg {
    width: 11px; height: 11px;
    margin: 3px 4px 0 0;
    flex: none;
    fill: var(--accent);
  }
</style>
</head>
<body>

<section class="card card-back">
  <div class="back-pattern" role="img" aria-label="Repeating pattern of brand symbols in shades of blue"></div>
  <div class="back-brand">TOVRIN</div>
</section>

<section class="card card-front">
  <div class="front-brand">TOVRIN</div>

  <div class="holder">
    <div class="holder-name">WARREN HALBECK</div>
    <div class="holder-role">General Manager</div>
  </div>

  <div class="divider"></div>

  <ul class="contacts">
    <li>
      <svg viewBox="0 0 12 12"><path d="M6 0a4 4 0 0 0-4 4c0 3 4 8 4 8s4-5 4-8a4 4 0 0 0-4-4zm0 5.6A1.6 1.6 0 1 1 6 2.4a1.6 1.6 0 0 1 0 3.2z"/></svg>
      <span>87 Marrow Ave<br>Pendlebay, QLD, 4023</span>
    </li>
    <li class="gap">
      <svg viewBox="0 0 12 12"><path d="M2.6 0.6l1.8 2.2-1 1.3a7 7 0 0 0 4.5 4.5l1.3-1 2.2 1.8-1 1.9C6 11.3 0.7 6 0.7 1.6z"/></svg>
      <span>0472 915 348</span>
    </li>
    <li>
      <svg viewBox="0 0 12 12"><path d="M0 2.5h12v7H0zM0.8 3.2L6 6.8l5.2-3.6"/><path d="M0.8 3.2L6 6.6l5.2-3.4" fill="none" stroke="#fff" stroke-width="1"/></svg>
      <span>Warren.halbeck@tovrin.com.au</span>
    </li>
    <li>
      <svg viewBox="0 0 12 12"><circle cx="6" cy="6" r="5.5"/><path d="M0.5 6h11M6 0.5c-2.5 3-2.5 8 0 11M6 0.5c2.5 3 2.5 8 0 11" fill="none" stroke="#fff" stroke-width="0.8"/></svg>
      <span>www.tovrin.com.au</span>
    </li>
  </ul>
</section>

</body>
</html>
```